International Business Development Firm, in need of Branded Stationery material

We just made our Logo and now we are looking for branded stationery for our company such as:

* A Letterhead with our company's name, address, and logo at the top in Word format for easy editing
* A more formal letter format with a light background design (watermark) featuring our logo, allowing us to write over it for various documents and presentations
* Business card + Envelopes are a plus but not a must
* PowerPoint for company and product introductions
* An Info sheet with Bullet Points

The design should be professional.
Please ensure the design is high quality and print ready.

Target Market(s)

Businesses and high net value individuels

Industry/Entity Type

International Business Development Firm

Colors

Designer to choose colors to be used in the design.

Requirements
Must have
• word docs so i can use the stationery templates afterwards

```html
<!DOCTYPE html>
<html lang="en">
<head>
<meta charset="utf-8">
<title>Violet Crest – Business Card</title>
<link href="https://fonts.googleapis.com/css2?family=Open+Sans:wght@400;700&display=swap" rel="stylesheet">
<style>
  :root {
    --backdrop: #e4ddd4;
    --card: #f1ede8;
    --card-edge: #d9d2ca;
    --brand-purple: #5a2a78;
    --muted-purple: #7d6391;
    --emblem: #8a6f9c;
    --ink: #3b3636;
  }
  html, body {
    margin: 0;
    width: 1200px;
    height: 1047px;
    overflow: hidden;
    background: var(--backdrop);
  }
  .canvas {
    position: relative;
    width: 1200px;
    height: 1047px;
  }
  .business-card {
    position: absolute;
    left: 151px;
    top: 291px;
    width: 946px;
    height: 516px;
    background: var(--card);
    border: 1px solid var(--card-edge);
    border-radius: 22px;
    font-family: "Open Sans", Arial, sans-serif;
    color: var(--ink);
    overflow: hidden;
  }
  .brand {
    position: absolute;
    left: 40px;
    top: 64px;
    display: flex;
    align-items: center;
    gap: 16px;
  }
  .brand-dot {
    width: 34px;
    height: 34px;
    border-radius: 50%;
    background: var(--brand-purple);
  }
  .brand-name {
    font-weight: 700;
    font-size: 40px;
    line-height: 52px;
    letter-spacing: 1px;
    color: var(--brand-purple);
    text-transform: uppercase;
  }
  .person-bar {
    position: absolute;
    left: 4px;
    top: 197px;
    width: 20px;
    height: 62px;
    background: var(--brand-purple);
  }
  .person {
    position: absolute;
    left: 40px;
    top: 193px;
  }
  .person-name {
    margin: 0;
    font-weight: 700;
    font-size: 36px;
    line-height: 40px;
    color: var(--brand-purple);
    text-transform: uppercase;
  }
  .person-title {
    margin: 0;
    font-size: 26px;
    line-height: 32px;
    color: var(--muted-purple);
    text-transform: uppercase;
  }
  .address {
    position: absolute;
    left: 37px;
    top: 296px;
    margin: 0;
    font-size: 26px;
    line-height: 33px;
    font-style: normal;
  }
  .contacts {
    position: absolute;
    left: 36px;
    top: 387px;
    margin: 0;
    padding: 0;
    list-style: none;
    font-size: 26px;
    line-height: 33px;
  }
  .contacts li {
    display: flex;
    align-items: center;
    gap: 9px;
  }
  .contacts svg {
    width: 22px;
    height: 22px;
    fill: var(--brand-purple);
  }
  .brand-emblem {
    position: absolute;
    left: 681px;
    top: 127px;
    width: 260px;
    height: 260px;
    border-radius: 50%;
    background: var(--emblem);
  }
</style>
</head>
<body>
<div class="canvas">
  <div class="business-card">
    <div class="brand">
      <span class="brand-dot"></span>
      <span class="brand-name">Violet Crest</span>
    </div>

    <span class="person-bar"></span>
    <div class="person">
      <p class="person-name">Marcus Hale</p>
      <p class="person-title">Managing Director</p>
    </div>

    <address class="address">Your address, City<br>State, Zip 1234</address>

    <ul class="contacts">
      <li>
        <svg viewBox="0 0 24 24" aria-hidden="true"><path d="M6.6 10.8a15.1 15.1 0 0 0 6.6 6.6l2.2-2.2a1 1 0 0 1 1-.25 11.4 11.4 0 0 0 3.6.57 1 1 0 0 1 1 1V20a1 1 0 0 1-1 1A17 17 0 0 1 3 4a1 1 0 0 1 1-1h3.5a1 1 0 0 1 1 1c0 1.25.2 2.45.57 3.57a1 1 0 0 1-.25 1z"/></svg>
        123 456 789
      </li>
      <li>
        <svg viewBox="0 0 24 24" aria-hidden="true"><path d="M3 5h18a1 1 0 0 1 1 1v12a1 1 0 0 1-1 1H3a1 1 0 0 1-1-1V6a1 1 0 0 1 1-1zm1 2.2V17h16V7.2l-8 5.3z M5 7l7 4.6L19 7z"/></svg>
        info@yourmail.com
      </li>
      <li>
        <svg viewBox="0 0 24 24" aria-hidden="true"><path d="M12 2a10 10 0 1 0 0 20 10 10 0 0 0 0-20zm-1 17.9A8 8 0 0 1 4.1 11H7c.1 3 1.5 6 4 8.9zM7 9H4.3A8 8 0 0 1 11 4.1C8.7 6.6 7.2 7.8 7 9zm6 10.9c2.5-2.9 3.9-5.9 4-8.9h2.9a8 8 0 0 1-6.9 8.9zM17 9c-.2-1.2-1.7-2.4-4-4.9A8 8 0 0 1 19.7 9z"/></svg>
        www.yourwebsite.com
      </li>
    </ul>

    <div class="brand-emblem"></div>
  </div>
</div>
</body>
</html>
```